Fitness Equipment Repair Business Needs a Catchy New Business Card

We have an existing business card, however, it is quite plain and boring. We are expanding primarily in the commercial area (gyms, studios, apartment complexes etc). The business card will serve as eye candy to those managers/owners that can't be met for a face to face.
Originally I was planning for a brochure as well, but all of our information is better summarized on our website. (brightloopservice.ca).
I would like the card to match the colour scheme of the website and utilize the logo. It should have a professional clean feel to it, however, a little colouring outside the lines wouldn't hurt.
The example card is for my service technician (Colin Marsh). If possible I would like to be able to edit the text to use for more than one person.

Industry/Entity Type

Appliance Repair

Contact Information for Business Card

Clean, crisp and professional but needs to be eye catching. Preferably using the black, white and red colour scheme matching the website. Double sided would be nice, but is not necessary.

Colors
ec1f27
ffffff
000000

Requirements
Must have
• Must be able to edit name, phone number and title to use for multiple people. Must show the company website (brightloopservice.ca).

```html
<!DOCTYPE html>
<html lang="en">
<head>
<meta charset="utf-8">
<title>Bright Loop Service – Business Card</title>
<link rel="stylesheet" href="https://fonts.googleapis.com/css2?family=Jost:wght@400;500;600&family=Michroma&display=swap">
<style>
  :root {
    --brand-red: #ec1f27;
    --brand-black: #000000;
    --brand-white: #ffffff;
    --backdrop: #7d6a5a;
    --art-dark: #111111;
    --art-mid: #2b2b2b;
  }
  * { margin: 0; padding: 0; box-sizing: border-box; }
  html, body {
    width: 1200px;
    height: 987px;
    overflow: hidden;
    background: var(--backdrop);
  }
  .stage {
    position: relative;
    width: 1200px;
    height: 987px;
  }

  /* Front: contact side */
  .card-front {
    position: absolute;
    left: 131px;
    top: 173px;
    width: 352px;
    height: 622px;
    background: var(--brand-red);
    color: var(--brand-white);
    overflow: hidden;
    text-align: center;
  }
  .person-name {
    position: absolute;
    top: 30px;
    left: 0;
    width: 100%;
    font-family: "Michroma", sans-serif;
    font-size: 21px;
    font-variant: small-caps;
    letter-spacing: 0.5px;
  }
  .person-title {
    position: absolute;
    top: 62px;
    left: 0;
    width: 100%;
    font-family: "Michroma", sans-serif;
    font-size: 14px;
    font-variant: small-caps;
    letter-spacing: 0.5px;
  }
  .address {
    position: absolute;
    top: 98px;
    left: 0;
    width: 100%;
    font-family: "Jost", sans-serif;
    font-size: 17px;
    line-height: 23px;
    font-style: normal;
  }
  .contact-list {
    position: absolute;
    top: 154px;
    left: 0;
    width: 100%;
    list-style: none;
    font-family: "Jost", sans-serif;
    font-size: 17px;
    line-height: 24px;
  }
  .contact-label { font-weight: 600; margin-right: 4px; }
  .mascot-art-front {
    position: absolute;
    left: 50px;
    top: 272px;
    width: 288px;
    height: 350px;
    border-radius: 120px 120px 0 0;
    background: linear-gradient(180deg, var(--art-mid), var(--art-dark));
  }

  /* Back: brand side */
  .card-back {
    position: absolute;
    left: 498px;
    top: 437px;
    width: 615px;
    height: 350px;
    background: var(--brand-black);
    color: var(--brand-white);
  }
  .mascot-art-back {
    position: absolute;
    left: 121px;
    top: 84px;
    width: 118px;
    height: 140px;
    border-radius: 50px 50px 6px 6px;
    background: linear-gradient(180deg, var(--art-mid), #1a1a1a);
  }
  .brand-initials {
    position: absolute;
    left: 124px;
    top: 226px;
    font-family: "Michroma", sans-serif;
    font-size: 24px;
    color: var(--brand-red);
  }
  .brand-name {
    position: absolute;
    left: 234px;
    top: 158px;
    font-family: "Michroma", sans-serif;
    font-size: 18px;
    font-variant: small-caps;
    letter-spacing: 1px;
  }
</style>
</head>
<body>
<main class="stage">
  <section class="card-front" aria-label="Business card front">
    <h1 class="person-name">Colin Marsh</h1>
    <p class="person-title">Service technician</p>
    <address class="address">1875 Larkfield Rd NW<br>Edmonton AB T5K 2P4</address>
    <ul class="contact-list">
      <li><span class="contact-label">P :</span>587-555-0148</li>
      <li><span class="contact-label">P :</span>780-555-0193</li>
      <li><span class="contact-label">E :</span>brightloop@mailbox.ca</li>
      <li>www.brightloopservice.ca</li>
    </ul>
    <div class="mascot-art-front" role="img" aria-label="Illustration of a muscular technician in a hard hat holding a wrench"></div>
  </section>

  <section class="card-back" aria-label="Business card back">
    <div class="mascot-art-back" role="img" aria-label="Small illustration of a muscular technician in a hard hat holding a wrench"></div>
    <span class="brand-initials">BLS</span>
    <p class="brand-name">Bright Loop Service</p>
  </section>
</main>
</body>
</html>
```